Legal firm website redesign

Existing site for Sydney CBD lawyer needs clean and professional redesign - http://brintonlaw.com.au

The site will be viewed by a wide range of users: businesses, individuals, referral partners and other lawyers.

Please see the list of must haves for further details

Target Market(s)

Businesses, individuals, referral partners and other lawyers

Industry/Entity Type

Lawyer

Requirements
Must have
• Prominent display of phone number.
List of services down the left hand side of the site (5x services or so).
Search box in header.
Please use the greys and blues from the existing header.
New header must include the wording "Efficiency - Fulfillment - Integrity - Teamwork"

```html
<!DOCTYPE html>
<html lang="en">
<head>
<meta charset="utf-8">
<title>Brinton Law</title>
<link href="https://fonts.googleapis.com/css2?family=Source+Sans+3:ital,wght@0,400;0,600;1,400&family=Arimo:ital,wght@0,400;0,700;1,400;1,700&family=PT+Sans+Narrow&display=swap" rel="stylesheet">
<style>
:root{
  --sky:#16b9ec;
  --sky-light:#7ddcfa;
  --blue:#1b86e0;
  --grey-dark:#595959;
  --grey-mid:#6a6a6a;
  --grey-text:#4a4a4a;
  --grey-body:#555;
  --grey-light:#ececec;
  --grey-row:#dedede;
  --white:#fff;
  --footer:#575757;
  --head-font:"Source Sans 3",sans-serif;
  --body-font:Arimo,Arial,sans-serif;
  --narrow-font:"PT Sans Narrow",sans-serif;
}
*{box-sizing:border-box;margin:0;padding:0}
html,body{width:1200px;height:1200px;overflow:hidden;background:var(--grey-light)}
.page{position:absolute;left:0;top:0;width:1024px;height:1024px;transform:scale(1.171875);transform-origin:0 0;font-family:var(--body-font);color:var(--grey-body)}
.sky-band{position:absolute;left:0;top:0;width:1024px;height:150px;background:linear-gradient(#0fb7ee,#19bcef 70%,#6fd2f3)}
.texture-band{position:absolute;left:0;top:150px;width:1024px;height:345px;background:#f3f3f3;border-bottom:1px solid #d8d8d8}
.header-card{position:absolute;left:111px;top:0;width:802px;height:107px;background:linear-gradient(#fff,#f1f1f1);border-radius:0 0 10px 10px}
.brand{position:absolute;left:14px;top:30px;display:flex;align-items:center;gap:10px;font-family:var(--head-font);font-weight:600;font-size:38px;color:var(--grey-dark)}
.brand-mark{width:26px;height:26px;background:var(--grey-dark)}
.follow{position:absolute;right:8px;top:10px;display:flex;align-items:center;gap:4px;font-family:var(--head-font);font-size:13px;color:var(--grey-text)}
.follow span{margin-right:6px}
.social-dot{width:28px;height:28px;border-radius:50%;background:#2f7fc9}
.social-dot.rss{background:#f07a1e}
.call-label{position:absolute;left:647px;top:50px;font-family:var(--head-font);font-size:16px;color:var(--blue)}
.phone-icon{position:absolute;left:602px;top:63px}
.phone-number{position:absolute;left:647px;top:64px;font-family:var(--head-font);font-size:25px;color:var(--grey-text)}
.search{position:absolute;left:111px;top:117px;width:162px;height:23px;border-radius:6px;background:linear-gradient(#fff,#e4e4e4);border:1px solid #9bbfd0;font-family:var(--body-font);font-style:italic;font-size:10px;color:#777;padding:5px 10px}
.search svg{position:absolute;right:4px;top:2px}
.nav{position:absolute;top:114px;height:29px;border-radius:4px;background:linear-gradient(#fff,#dcdcdc);font-family:var(--head-font);font-size:15px;color:var(--grey-text);display:flex;align-items:center;justify-content:center}
.nav.active{background:linear-gradient(#7a7a7a,#5a5a5a);color:#fff}
.area-panel{position:absolute;left:111px;top:156px;width:188px;height:297px;background:linear-gradient(#5f5f5f,#545454);border-radius:4px}
.area-title{position:absolute;left:10px;top:12px;font-family:var(--head-font);font-style:italic;font-size:25px;color:#fff}
.area-item{position:absolute;left:0;width:180px;height:33px;background:linear-gradient(#fdfdfd,#cfcfcf);clip-path:polygon(0 0,164px 0,180px 50%,164px 100%,0 100%);font-family:var(--narrow-font);font-size:14px;color:#333;padding:8px 9px}
.hero{position:absolute;left:316px;top:156px;width:597px;height:297px;border-radius:4px;overflow:hidden;background:linear-gradient(#8a2a14 0%,#5e1a0c 45%,#7a4a24 52%,#3e2312 100%)}
.hero-caption{position:absolute;left:0;bottom:0;width:100%;height:57px;background:rgba(236,236,236,.9);font-family:var(--head-font);font-size:29px;color:#333;text-align:center;line-height:57px}
.hero-dots{position:absolute;right:14px;top:229px;display:flex;gap:7px}
.hero-dots i{width:19px;height:19px;border-radius:50%;background:var(--sky);border:2px solid #fff;box-shadow:0 0 0 1px #0a6a90}
.hero-dots i.on{background:#0b6f98}
.hero-shadow{position:absolute;left:140px;top:458px;width:760px;height:20px;border-radius:50%;background:radial-gradient(rgba(0,0,0,.12),transparent 70%)}
.section-title{position:absolute;font-family:var(--head-font);font-style:italic;font-size:24px;color:var(--grey-text)}
.section-title b{font-weight:400;color:var(--blue)}
.welcome-photo{position:absolute;left:111px;top:554px;width:119px;height:114px;background:linear-gradient(#b8b8b8,#4c4c4c)}
.welcome-text{position:absolute;left:248px;top:548px;width:324px;font-size:12px;line-height:19.7px;text-align:justify}
.btn{position:absolute;border-radius:5px;background:linear-gradient(#fafafa,#d6d6d6);border:1px solid #bbb;font-family:var(--head-font);font-weight:600;font-size:13px;color:#333;display:flex;align-items:center;justify-content:center}
.rule{position:absolute;left:111px;top:696px;width:461px;height:1px;background:#c8c8c8}
.divider{position:absolute;left:616px;top:508px;width:1px;height:382px;background:#c8c8c8}
.news{position:absolute;left:111px;width:215px;font-size:11px;line-height:15.5px}
.news em{font-family:var(--head-font);font-size:15px;color:#333;margin-right:4px}
.quote{position:absolute;left:368px;top:739px;width:192px;font-style:italic;font-size:11px;line-height:15.6px}
.quote .mark{position:absolute;left:0;top:0;font-size:34px;color:#aaa;font-weight:700;line-height:30px}
.read-all{position:absolute;left:368px;top:839px;font-style:italic;font-size:11px;color:var(--blue)}
.author{position:absolute;left:500px;top:839px;width:70px;text-align:right;font-style:italic;font-weight:700;font-size:11px;color:#333;line-height:15.5px}
.pager{position:absolute;top:880px;width:68px;height:19px;border-radius:4px;background:var(--grey-dark);display:flex;justify-content:space-around;align-items:center}
.pager i{width:15px;height:15px;border-radius:50%;background:#eee;position:relative}
.pubs-head{position:absolute;left:657px;top:508px;width:256px;height:41px;background:var(--grey-dark)}
.pubs-head h2{position:absolute;left:12px;top:7px;font-family:var(--head-font);font-style:italic;font-weight:400;font-size:25px;color:#fff}
.pubs-head .arrows{position:absolute;right:10px;top:11px;display:flex;gap:8px}
.pubs-head .arrows i{width:17px;height:17px;border-radius:50%;background:#eee}
.pub{position:absolute;left:657px;width:256px;height:41px;font-size:11.5px;line-height:15px;color:#333;padding:5px 0 0 29px;border-top:1px solid #c4c4c4}
.pub:nth-of-type(odd){background:var(--grey-row)}
.pub.white{background:#fff}
.pub::before{content:"››";position:absolute;left:9px;top:3px;font-weight:700;font-size:13px}
.footer{position:absolute;left:0;top:908px;width:1024px;height:116px;background:var(--footer);color:#fff}
.foot-links{position:absolute;left:111px;top:27px;font-size:10px}
.foot-links span{margin:0 5px;color:#ccc}
.copyright{position:absolute;left:111px;top:68px;font-size:10px;line-height:13px;color:#ddd}
.foot-title{position:absolute;font-family:var(--head-font);font-size:16px;font-weight:600}
.email-field{position:absolute;left:452px;top:36px;width:189px;height:23px;border-radius:5px;background:#777;border:1px solid #999;font-style:italic;font-size:10px;color:#ccc;padding:5px 10px}
.contact{position:absolute;left:741px;top:32px;font-size:10px;line-height:13.6px}
</style>
</head>
<body>
<div class="page">
  <div class="sky-band"></div>
  <div class="texture-band"></div>

  <header class="header-card">
    <div class="brand"><span class="brand-mark"></span>Brinton Law</div>
    <div class="follow"><span>Follow us on:</span><i class="social-dot"></i><i class="social-dot"></i><i class="social-dot"></i><i class="social-dot rss"></i></div>
    <div class="call-label">Call Us:</div>
    <svg class="phone-icon" width="36" height="32" viewBox="0 0 36 32">
      <path d="M2 9 Q18 -1 34 9 L31 14 L25 12 L24 8 Q18 6 12 8 L11 12 L5 14 Z" fill="#555"/>
      <rect x="7" y="15" width="22" height="13" rx="3" fill="#555"/>
      <circle cx="18" cy="21" r="4" fill="#ddd"/>
    </svg>
    <div class="phone-number">(02) 9470 3362</div>
  </header>

  <div class="search">Place search here...
    <svg width="22" height="18" viewBox="0 0 22 18"><circle cx="8" cy="7" r="5.5" fill="none" stroke="#444" stroke-width="2"/><path d="M12 11 L19 16" stroke="#444" stroke-width="3"/></svg>
  </div>
  <nav>
    <div class="nav active" style="left:462px;width:61px">Home</div>
    <div class="nav" style="left:533px;width:74px">About Us</div>
    <div class="nav" style="left:618px;width:91px">Area of Law</div>
    <div class="nav" style="left:719px;width:91px">Publications</div>
    <div class="nav" style="left:821px;width:92px">Contact Us</div>
  </nav>

  <aside class="area-panel">
    <div class="area-title">Area of Law</div>
    <div class="area-item" style="top:52px">Commercial Transactions</div>
    <div class="area-item" style="top:97px">Business Transactions</div>
    <div class="area-item" style="top:143px">Commercial Litigation</div>
    <div class="area-item" style="top:188px">Estate Planning &amp; Succession</div>
  </aside>

  <section class="hero" role="img" aria-label="Photo of scales of justice, a law book and a gavel on a wooden desk before a red curtain">
    <div class="hero-dots"><i class="on"></i><i></i><i></i><i></i></div>
    <div class="hero-caption">Efficiency - Fulfillment - Integrity - Teamwork</div>
  </section>
  <div class="hero-shadow"></div>

  <h1 class="section-title" style="left:111px;top:515px"><b>Welcome to</b> Brinton Law</h1>
  <div class="welcome-photo" role="img" aria-label="Photo of the word Justice carved in stone"></div>
  <p class="welcome-text">Brinton Law is a dynamic commercial law firm in the CBD of Sydney providing services to corporate, small business and private clients. Brinton Law brings together over 30 years of experience in legal practice. The strong focus of the firm is on commercial law and estate planning.</p>
  <div class="btn" style="left:498px;top:651px;width:74px;height:28px">Read More</div>
  <div class="rule"></div>
  <div class="divider"></div>

  <h2 class="section-title" style="left:111px;top:705px"><b>Latest</b> News</h2>
  <h2 class="section-title" style="left:366px;top:705px"><b>Client’s</b> Testimonials</h2>
  <p class="news" style="top:742px"><em>Mar- 10- 2012</em>Lorem ipsum dolor sit amet, consectetuer adipiscing eraesent vestibulum molestie nonummy</p>
  <p class="news" style="top:819px"><em>Mar- 10- 2012</em>Lorem ipsum dolor sit amet, consectetuer adipiscing eraesent vestibulum molestie nonummy</p>
  <div class="quote"><span class="mark">“</span><span style="padding-left:30px">Phasellus portafusce suscipit</span> varius mi sociis natoque penatibuset magnis dis parturient montes nascetur ridiculus mulla ducuscegiat malesuada odio morbi nunc odio, gravida at cursus......</div>
  <div class="read-all">Read All</div>
  <div class="author">By Daniel<br>CEO</div>
  <div class="pager" style="left:111px"><i></i><i></i></div>
  <div class="pager" style="left:384px"><i></i><i></i></div>

  <div class="pubs-head"><h2>Publications</h2><div class="arrows"><i></i><i></i></div></div>
  <div class="pub" style="top:561px;background:var(--grey-row)">Commencement of the Succession Act 2006 25.03.08</div>
  <div class="pub white" style="top:602px">Is that will valid?<br>15.01.08</div>
  <div class="pub" style="top:643px;background:var(--grey-row)">Labor's proposed changes to IR laws<br>14.12.07</div>
  <div class="pub white" style="top:684px">Should you make your own will?<br>14.11.07</div>
  <div class="pub" style="top:724px;background:var(--grey-row)">Illegal workers<br>14.08.07</div>
  <div class="pub white" style="top:765px">Employees' liability for misleading or deceptive conduct 14.08.07</div>
  <div class="pub" style="top:805px;background:var(--grey-row)">Correct use of ACNs and ABNs<br>14.08.07</div>
  <div class="pub white" style="top:846px;height:43px">Power of Attorney Infosheet<br>10.08.07</div>

  <footer class="footer">
    <div class="foot-links">Home<span>|</span>About Us<span>|</span>Area of Law<span>|</span>Our People<span>|</span>Publication<span>|</span>Contact</div>
    <div class="copyright">Copyright © 2012 By Brinton Law<br>All rights reserved.</div>
    <div class="foot-title" style="left:452px;top:10px">Newsletter SignUp</div>
    <div class="email-field">Enter Email Address</div>
    <div class="btn" style="left:566px;top:68px;width:74px;height:28px">Subscribe</div>
    <div class="foot-title" style="left:741px;top:10px">Contact Us</div>
    <div class="contact">Brinton Law Pty Ltd<br>Level 4, 120 Clarence St, Sydney NSW 2000<br>Telephone: (02) 9470 3362<br>Facsimile: (02) 9470 3363<br>info@brintonlaw.com.au</div>
  </footer>
</div>
</body>
</html>
```